A private security company called "Tavron Security Services Ltd"

Hello everybody,

We need a web page for a company based in NZ. It is mainly an informative website so it would be wonderful if the designer puts their absolute best into making it a website that I would really appreciate. The website needs to show professionalism and also needs to make our web surfers find the information they need in a click. the company's colour is black and silver, and if those two colours could be integrated into the website it would be absolutely lovely. Please do contact me for any information.

Sincerely,
Dorian Vaskel

Industry/Entity Type

Security

```html
<!DOCTYPE html>
<html lang="en">
<head>
<meta charset="utf-8">
<title>Tavron Security Services Ltd</title>
<link rel="stylesheet" href="https://fonts.googleapis.com/css2?family=Raleway:wght@500&family=Source+Sans+3:wght@400;600&display=swap">
<style>
:root{
  --ink:#1f1f1f;
  --charcoal:#3d3f42;
  --text:#555;
  --muted:#888;
  --silver:#d9d9d9;
  --panel:#f4f4f4;
  --white:#fff;
  --accent:#e8661b;
}
*{margin:0;padding:0;box-sizing:border-box}
html,body{width:1152px;height:1200px;overflow:hidden;background:var(--white)}
body{position:relative;font-family:"Source Sans 3",sans-serif;color:var(--ink)}
.topline{position:absolute;left:0;top:0;width:1152px;height:5px;background:var(--ink)}
.brand{position:absolute;left:101px;top:38px;display:flex;align-items:center;gap:10px}
.brand-mark{width:26px;height:26px;background:var(--ink)}
.brand-name{font-family:"Source Sans 3",sans-serif;font-weight:600;font-size:17px;line-height:20px;color:var(--ink);letter-spacing:.5px;text-transform:uppercase}
.search{position:absolute;left:892px;top:19px;width:140px;height:30px;border:1px solid #cfcfcf;border-radius:3px;background:#f3f3f3;font-family:"Raleway",sans-serif;font-size:12px;color:#999;padding:7px 8px}
.search-icon{position:absolute;left:1037px;top:25px}
.nav{position:absolute;top:70px;left:0;width:1152px;height:34px}
.nav a{position:absolute;top:0;height:34px;line-height:34px;font-family:"Raleway",sans-serif;font-weight:500;font-size:15.5px;color:var(--ink);text-decoration:none;letter-spacing:.3px}
.nav .active{left:472px;width:78px;text-align:center;background:var(--ink);color:var(--white);border-radius:6px}
.hero{position:absolute;left:0;top:115px;width:1152px;height:447px;background:linear-gradient(90deg,#9a9a9a 0%,#5e5e5e 30%,#7d7d7d 55%,#4f4f4f 78%,#a5a5a5 100%)}
.hero-arrow{position:absolute;top:308px;width:58px;height:58px;border-radius:50%;background:rgba(70,70,70,.85)}
.welcome{position:absolute;left:96px;top:590px;width:650px}
.welcome h1{font-weight:600;font-size:24px;letter-spacing:1px;color:var(--ink)}
.welcome p{margin-top:14px;font-family:Arial,sans-serif;font-size:13.4px;line-height:19.2px;color:var(--text);padding-left:2px;width:642px}
.welcome p+p{margin-top:19px}
.learn{position:absolute;left:98px;top:792px;font-family:"Raleway",sans-serif;font-size:13.5px;color:#333;display:flex;align-items:center;gap:9px}
.learn span.box{width:18px;height:18px;background:var(--charcoal);display:inline-flex;align-items:center;justify-content:center}
.services{position:absolute;left:758px;top:592px;width:320px;height:196px;border-left:3px dotted #c8c8c8}
.services .gear{position:absolute;left:13px;top:-5px}
.services h2{position:absolute;left:59px;top:0;font-weight:600;font-size:24px;letter-spacing:1px}
.services ul{position:absolute;left:18px;top:40px;list-style:none}
.services li{position:relative;font-family:Arial,sans-serif;font-size:12.4px;color:#222;height:28.8px;line-height:28px;padding-left:17px;width:183px;border-bottom:1px solid #d8d8d8;white-space:nowrap}
.services li:last-child{border-bottom:none}
.services li::before{content:"";position:absolute;left:6px;top:12px;width:5px;height:5px;border-radius:50%;background:#555}
.lower{position:absolute;left:0;top:834px;width:1152px;height:316px;background:var(--panel)}
.col-title{position:absolute;top:26px;font-size:21.5px;font-weight:400;color:#333}
.news-title{position:absolute;left:124px;top:72px;font-weight:600;font-size:17px;color:#333}
.news-date{position:absolute;left:124px;top:96px;font-size:13px;color:var(--muted)}
.news-date sup{font-size:8px}
.news-body{position:absolute;left:124px;top:120px;width:270px;font-size:12.4px;line-height:22px;color:#444}
.full{position:absolute;left:124px;top:252px;font-size:12.5px;letter-spacing:.8px;color:#777}
.tweets{position:absolute;left:420px;top:76px;width:262px;height:209px;border:1px solid #d6d6d6;background:var(--panel)}
.tweet{height:95px;padding:16px 18px 0;font-size:12.2px;line-height:19px;color:#333;border-bottom:1px solid #d6d6d6}
.tweet:last-child{border-bottom:none}
.tweet .handle{color:#777}
.tweet .ago{display:block;margin-top:6px;font-size:11px;color:#888}
.dots{position:absolute;left:997px;top:61px;display:flex;gap:4px}
.dots i{width:5px;height:5px;border-radius:50%;background:#d0d0d0}
.dots i:last-child{background:#777}
.quote{position:absolute;left:704px;top:76px;width:322px;height:170px;background:var(--white);border:1px solid #d6d6d6;padding:28px 32px;font-size:12.2px;line-height:22.5px;color:#333}
.quote .mark{position:absolute;right:16px;bottom:12px;font-size:30px;line-height:20px;color:#444;font-weight:600}
.quote-tail{position:absolute;left:989px;top:245px}
.author{position:absolute;right:129px;top:265px;font-size:12.4px;color:#333}
.author b{font-weight:600}
.author em{font-style:normal;color:var(--accent)}
.footer{position:absolute;left:0;top:1150px;width:1152px;height:50px;background:var(--charcoal);color:var(--white)}
.footer-links{position:absolute;left:128px;top:16px;font-size:12.4px;display:flex}
.footer-links span{padding:0 14px;border-left:1px solid #ccc;line-height:14px}
.footer-links span:first-child{padding-left:0;border-left:none}
.copy{position:absolute;right:96px;top:16px;font-family:Arial,sans-serif;font-size:13.4px}
</style>
</head>
<body>
<div class="topline"></div>

<header>
  <div class="brand"><span class="brand-mark"></span><span class="brand-name">Tavron<br>Security Services Ltd.</span></div>
  <div class="search">search</div>
  <svg class="search-icon" width="18" height="18" viewBox="0 0 18 18"><circle cx="7.5" cy="7.5" r="5.5" fill="none" stroke="#111" stroke-width="2.4"/><line x1="11.5" y1="11.5" x2="16" y2="16" stroke="#111" stroke-width="2.8" stroke-linecap="round"/></svg>
  <nav class="nav">
    <a class="active" href="#">HOME</a>
    <a href="#" style="left:596px">ABOUT</a>
    <a href="#" style="left:713px">SERVICES</a>
    <a href="#" style="left:851px">BLOG</a>
    <a href="#" style="left:956px">CONTACT US</a>
  </nav>
</header>

<section class="hero" role="img" aria-label="Black and white photo of two uniformed security guards standing at a glass building entrance">
  <span class="hero-arrow" style="left:7px"><svg width="58" height="58" viewBox="0 0 58 58"><path d="M33 20 L24 29 L33 38" fill="none" stroke="#ddd" stroke-width="4"/></svg></span>
  <span class="hero-arrow" style="left:1070px"><svg width="58" height="58" viewBox="0 0 58 58"><path d="M25 20 L34 29 L25 38" fill="none" stroke="#ddd" stroke-width="4"/></svg></span>
</section>

<section class="welcome">
  <h1>Welcome to Tavron Security Services Ltd.</h1>
  <p>Lorem Ipsum is simply dummy text of the printing and typesetting industry. Lorem Ipsum has been the industry's standard dummy text ever since the 1500s, when an unknown printer took a galley of type and scrambled it to make a type specimen book. It has survived not only five centuries, but also the leap into electronic typesetting, remaining essentially unchanged. It was popularised in the 1960s with</p>
  <p>The release of Letraset sheets containing Lorem Ipsum passages, and more recently with desktop publishing software like Aldus PageMaker including versions of Lorem Ipsum.</p>
</section>
<a class="learn">Learn More <span class="box"><svg width="8" height="10" viewBox="0 0 8 10"><path d="M2 1 L6 5 L2 9" fill="none" stroke="#fff" stroke-width="2"/></svg></span></a>

<aside class="services">
  <svg class="gear" width="40" height="40" viewBox="0 0 40 40"><circle cx="20" cy="20" r="19" fill="#fff" stroke="#e2e2e2"/><g fill="#333"><circle cx="20" cy="20" r="9"/><rect x="17.5" y="7" width="5" height="26"/><rect x="7" y="17.5" width="26" height="5"/><rect x="17.5" y="7" width="5" height="26" transform="rotate(45 20 20)"/><rect x="17.5" y="7" width="5" height="26" transform="rotate(-45 20 20)"/></g><circle cx="20" cy="20" r="4" fill="#fff"/></svg>
  <h2>Our Services</h2>
  <ul>
    <li>Property guards</li>
    <li>Corporate events security</li>
    <li>personal bodyguard for high net worth individuals</li>
    <li>security consultancy</li>
    <li>private investigation</li>
  </ul>
</aside>

<section class="lower">
  <h3 class="col-title" style="left:125px">Latest News</h3>
  <h3 class="col-title" style="left:423px">Recent Tweets</h3>
  <h3 class="col-title" style="left:708px">Our Client's are Awesome</h3>

  <div class="news-title">Lorem ipsum dolor sit amet</div>
  <div class="news-date">14<sup>th</sup> November</div>
  <p class="news-body">Nam libero tempore, cum soluta nobis est eligendi optio cumque nihil impedit quo lorem ipsum dolor sit&nbsp; minus id quod maxime placeat facere possimus, omnis voluptas assumenda est, omnis dolor repellendus...</p>
  <div class="full">FULL ARTICLE &nbsp;&nbsp;›</div>

  <div class="tweets">
    <div class="tweet"><span class="handle">@quietharbor</span> Lorem ipsum dolor sit amet consectetur adipisicing elit.<span class="ago">9 hours ago</span></div>
    <div class="tweet"><span class="handle">@northbeacon</span> At vero eos et accusamus et iusto odio dignissimos ducimus blanditiis praesentium voluptatum<span class="ago">1 day ago</span></div>
  </div>

  <div class="dots"><i></i><i></i><i></i></div>
  <div class="quote">At vero eos et accusamus et lucero iusto odio dignissimos ducimus qui blanditiis praesentium voluptatum deleniti atque corrupti quos dolores et quas molestias excepturi sint occaecati cupiditate non provident.<span class="mark">”</span></div>
  <svg class="quote-tail" width="22" height="12" viewBox="0 0 22 12"><path d="M0 0 L11 11 L22 0" fill="#fff" stroke="#d6d6d6"/><line x1="1" y1="0" x2="21" y2="0" stroke="#fff" stroke-width="2"/></svg>
  <div class="author"><b>John Doe</b>, <em>xyz etc.</em>, cat lover</div>
</section>

<footer class="footer">
  <div class="footer-links"><span>Home</span><span>About Us</span><span>Products</span><span>News &amp; Blog</span><span>Contact Us</span></div>
  <div class="copy">© 2014 . All right reserved. Privacy Policy | &nbsp;Terms &amp; Conditions</div>
</footer>
</body>
</html>
```